Acupuncture business needs business card design

I need a business card for an acupuncture clinic called "Harbourlight Wellness"
It will need the following details:
My name: Marcus Pelling
Acupuncturist
Member TVBH
KWF Treatment Provider
Ph numbers: 581 2734 027 418 5620
Email: marcus@hbwel.example.nz
On the back it will need a table with 2 columns for appointments, one column for time and one for date.

Industry/Entity Type

Clinic

Contact Information for Business Card

Marcus Pelling
Acupuncturist
Member TVBH
KWF Treatment Provider
Email: marcus@hbwel.example.nz

Requirements
Must have
• Marcus Pelling
• Acupuncturist
• Member TVBH
• KWF Treatment Provider
• Ph numbers: 581 2734 027 418 5620
• Email: marcus@hbwel.example.nz
• On the back it will need a table with 2 columns for appointments, one column for time and one for date.

```html
<!DOCTYPE html>
<html lang="en">
<head>
<meta charset="utf-8">
<title>Harbourlight Wellness – Business Card</title>
<link rel="stylesheet" href="https://fonts.googleapis.com/css2?family=Open+Sans:wght@400;600;700&display=swap">
<style>
  :root {
    --teal-deep: #1a6f84;
    --teal-card: #13809a;
    --cyan: #12a7d6;
    --ink-logo: #1b7c95;
    --tagline: #3fa9cf;
    --white: #ffffff;
    --bar: #cfe3ea;
    --backdrop: #e9ecee;
  }
  * { box-sizing: border-box; margin: 0; padding: 0; }
  html, body { width: 1200px; height: 948px; overflow: hidden; }
  body {
    background: var(--backdrop);
    font-family: "Open Sans", Arial, sans-serif;
    display: flex;
    flex-direction: column;
    align-items: center;
    justify-content: center;
    gap: 56px;
  }
  .card {
    position: relative;
    width: 680px;
    height: 390px;
    overflow: hidden;
    box-shadow: 0 6px 18px rgba(0,0,0,0.18);
  }

  /* Front */
  .card--front { background: var(--white); }
  .brand {
    position: absolute;
    left: 250px;
    top: 48px;
    display: flex;
    align-items: center;
    gap: 14px;
  }
  .brand__dot {
    width: 46px; height: 46px;
    border-radius: 50%;
    background: var(--ink-logo);
    flex: none;
  }
  .brand__name {
    color: var(--ink-logo);
    font-weight: 600;
    font-size: 33px;
    line-height: 1;
    letter-spacing: -0.3px;
  }
  .brand__tagline {
    position: absolute;
    left: 312px;
    top: 100px;
    color: var(--tagline);
    font-size: 12.5px;
    letter-spacing: 5.2px;
    text-transform: uppercase;
  }
  .band-identity {
    position: absolute;
    left: 0;
    top: 160px;
    width: 390px;
    height: 96px;
    background: var(--teal-deep);
    color: var(--white);
    padding: 16px 0 0 40px;
  }
  .band-identity__name {
    font-weight: 700;
    font-size: 19px;
    margin-bottom: 6px;
  }
  .band-identity__role {
    font-size: 13.5px;
    line-height: 1.4;
  }
  .band-contact {
    position: absolute;
    left: 300px;
    right: 0;
    top: 256px;
    height: 100px;
    background: var(--cyan);
    color: var(--white);
    padding: 20px 0 0 26px;
    font-size: 17px;
  }
  .contact-line {
    display: flex;
    align-items: center;
    gap: 14px;
    height: 30px;
  }
  .contact-line svg { width: 20px; height: 20px; flex: none; }

  /* Back */
  .card--back { background: var(--teal-card); }
  .appointments {
    position: absolute;
    left: 70px;
    top: 58px;
    border-collapse: separate;
    border-spacing: 22px 18px;
  }
  .appointments th {
    color: var(--white);
    font-weight: 400;
    font-size: 17px;
    text-align: left;
    padding-bottom: 0;
  }
  .appointments td {
    width: 230px;
    height: 26px;
    background: var(--bar);
    opacity: 0.85;
  }
  .web {
    position: absolute;
    right: 60px;
    bottom: 38px;
    color: var(--white);
    font-size: 19px;
    letter-spacing: 3px;
  }
</style>
</head>
<body>

  <section class="card card--front" aria-label="Business card front">
    <div class="brand">
      <span class="brand__dot"></span>
      <span class="brand__name">Harbourlight Wellness</span>
    </div>
    <div class="brand__tagline">Acupuncture Physiotherapy</div>

    <div class="band-identity">
      <div class="band-identity__name">Marcus Pelling</div>
      <div class="band-identity__role">Acupuncturist, Member TVBH</div>
      <div class="band-identity__role">KWF Treatment Provider</div>
    </div>

    <div class="band-contact">
      <div class="contact-line">
        <svg viewBox="0 0 20 20" aria-hidden="true">
          <circle cx="10" cy="10" r="10" fill="#ffffff"/>
          <path d="M7.2 5.2l1.6 2.4-1 1.1c.6 1.3 1.5 2.2 2.6 2.8l1.1-1 2.4 1.6-.9 1.9c-3.4-.4-6.3-3.3-6.7-6.9z" fill="#12a7d6"/>
        </svg>
        <span>581 2734 / 027 418 5620</span>
      </div>
      <div class="contact-line">
        <svg viewBox="0 0 20 20" aria-hidden="true">
          <circle cx="10" cy="10" r="10" fill="#ffffff"/>
          <rect x="5" y="6.5" width="10" height="7" fill="none" stroke="#12a7d6" stroke-width="1.4"/>
          <path d="M5 6.5l5 4 5-4" fill="none" stroke="#12a7d6" stroke-width="1.4"/>
        </svg>
        <span>marcus@hbwel.example.nz</span>
      </div>
    </div>
  </section>

  <section class="card card--back" aria-label="Business card back">
    <table class="appointments">
      <thead>
        <tr><th>Date</th><th>Time</th></tr>
      </thead>
      <tbody>
        <tr><td></td><td></td></tr>
        <tr><td></td><td></td></tr>
        <tr><td></td><td></td></tr>
        <tr><td></td><td></td></tr>
      </tbody>
    </table>
    <div class="web">www.hbwel.example.nz</div>
  </section>

</body>
</html>
```